Working Capital graphics

Our business advisory firm requires 9 images to be re-created and improved in the branding of our business.

The 9 images have been uploaded below and the colours and branding of the business can be found at the website www.tallowmereadvisory.com.au

```html
<!DOCTYPE html>
<html lang="en">
<head>
<meta charset="utf-8">
<title>Working Capital Levers Along the Value Chain</title>
<link rel="stylesheet" href="https://fonts.googleapis.com/css2?family=Catamaran:wght@600;700&display=swap">
<style>
  :root {
    --frame: #d4d4d4;
    --paper: #ffffff;
    --inventory: #1b4fb8;
    --payables: #f7941d;
    --receivables: #0db3f5;
    --connector: #1b3c8c;
    --label: #ffffff;
    --legend-text: #1b3c8c;
  }
  html, body {
    margin: 0;
    padding: 0;
    width: 1200px;
    height: 654px;
    overflow: hidden;
    background: var(--frame);
  }
  .value-chain {
    display: block;
    width: 1200px;
    height: 654px;
    font-family: "Catamaran", "Trebuchet MS", sans-serif;
    font-weight: 700;
  }
  .paper { fill: var(--paper); }
  .stage { fill: var(--inventory); }
  .stage-label { fill: var(--label); font-size: 30px; text-anchor: middle; letter-spacing: 0.5px; }
  .connector { stroke: var(--connector); stroke-width: 4; fill: none; }
  .lever-payables { fill: var(--payables); }
  .lever-receivables { fill: var(--receivables); }
  .lever-label { fill: var(--label); text-anchor: middle; letter-spacing: 0.5px; }
  .lever-label.large { font-size: 29px; }
  .lever-label.medium { font-size: 24px; }
  .lever-label.small { font-size: 21px; }
  .legend-dot-inventory { fill: var(--inventory); }
  .legend-dot-payables { fill: var(--payables); }
  .legend-dot-receivables { fill: var(--receivables); }
  .legend-label { fill: var(--legend-text); font-size: 23px; font-weight: 600; }
</style>
</head>
<body>
<svg class="value-chain" viewBox="0 0 2576 1404" xmlns="http://www.w3.org/2000/svg" role="img" aria-label="Working capital levers along the value chain from design to after sales service">
  <rect class="paper" x="11" y="11" width="2554" height="1382"/>

  <!-- connectors -->
  <g class="connectors">
    <line class="connector" x1="252" y1="557" x2="252" y2="647"/>
    <line class="connector" x1="754" y1="309" x2="754" y2="357"/>
    <line class="connector" x1="754" y1="557" x2="754" y2="647"/>
    <polyline class="connector" points="494,647 494,602 1014,602 1014,557"/>
    <line class="connector" x1="1648" y1="557" x2="1648" y2="647"/>
    <line class="connector" x1="2054" y1="309" x2="2054" y2="357"/>
    <line class="connector" x1="2054" y1="557" x2="2054" y2="647"/>
    <line class="connector" x1="2314" y1="557" x2="2314" y2="647"/>
    <line class="connector" x1="754" y1="893" x2="754" y2="961"/>
    <line class="connector" x1="2054" y1="893" x2="2054" y2="961"/>
    <line class="connector" x1="2314" y1="893" x2="2314" y2="961"/>
  </g>

  <!-- process stages -->
  <g class="stages">
    <polygon class="stage" points="133,647 373,647 423,770 378,893 133,893"/>
    <polygon class="stage" points="388,647 620,647 670,770 625,893 393,893 436,770"/>
    <polygon class="stage" points="635,647 872,647 922,770 877,893 640,893 683,770"/>
    <polygon class="stage" points="890,647 1140,647 1190,770 1145,893 895,893 938,770"/>
    <polygon class="stage" points="1155,647 1393,647 1443,770 1398,893 1160,893 1203,770"/>
    <polygon class="stage" points="1405,647 1645,647 1695,770 1650,893 1410,893 1453,770"/>
    <polygon class="stage" points="1655,647 1895,647 1945,770 1900,893 1660,893 1703,770"/>
    <polygon class="stage" points="1905,647 2143,647 2193,770 2148,893 1910,893 1953,770"/>
    <polygon class="stage" points="2155,647 2393,647 2443,770 2398,893 2160,893 2203,770"/>

    <text class="stage-label" x="278" y="793">DESIGN</text>
    <text class="stage-label" x="528"><tspan x="528" y="756">ORDER/</tspan><tspan x="528" y="788">MATERIAL</tspan><tspan x="528" y="819">PLANNING</tspan></text>
    <text class="stage-label" x="803" y="793">PURCHASING</text>
    <text class="stage-label" x="1059" y="786">MANUFACTURING</text>
    <text class="stage-label" x="1324" y="793">PRE-ASSEMBLY</text>
    <text class="stage-label" x="1565" y="786">ASSEMBLY</text>
    <text class="stage-label"><tspan x="1811" y="779">PACKAGING/</tspan><tspan x="1811" y="811">SHIPPING</tspan></text>
    <text class="stage-label" x="2043" y="786">SALES</text>
    <text class="stage-label"><tspan x="2316" y="779">AFTER&#160;&#160;SALES/</tspan><tspan x="2316" y="811">SERVICE</tspan></text>
  </g>

  <!-- levers -->
  <g class="levers">
    <circle class="lever-payables" cx="252" cy="457" r="100"/>
    <text class="lever-label small"><tspan x="252" y="438">REDUCE PART</tspan><tspan x="252" y="464">VARIANTS/</tspan><tspan x="252" y="490">RELEASES</tspan></text>

    <circle class="lever-receivables" cx="754" cy="209" r="100"/>
    <text class="lever-label large"><tspan x="754" y="185">MODIFY</tspan><tspan x="754" y="217">PAYMENT</tspan><tspan x="754" y="249">CONDITIONS</tspan></text>

    <circle class="lever-receivables" cx="754" cy="457" r="100"/>
    <text class="lever-label large"><tspan x="754" y="434">OPTIMIZE</tspan><tspan x="754" y="466">PAYMENT</tspan><tspan x="754" y="497">PROCESSES</tspan></text>

    <circle class="lever-payables" cx="1014" cy="457" r="100"/>
    <text class="lever-label small"><tspan x="1011" y="414">RETHINK</tspan><tspan x="1014" y="439">DELIVERY</tspan><tspan x="1011" y="463">SCHEDULES</tspan><tspan x="1011" y="488">AND</tspan><tspan x="1014" y="512">WAREHOUSING</tspan></text>

    <circle class="lever-payables" cx="1648" cy="457" r="100"/>
    <text class="lever-label large"><tspan x="1648" y="434">OPTIMIZE</tspan><tspan x="1648" y="466">PRODUCT</tspan><tspan x="1648" y="497">TESTING</tspan></text>

    <circle class="lever-receivables" cx="2054" cy="209" r="100"/>
    <text class="lever-label large"><tspan x="2054" y="185">IMPROVE</tspan><tspan x="2054" y="217">PAYMENT</tspan><tspan x="2054" y="249">SCHEMES</tspan></text>

    <circle class="lever-receivables" cx="2054" cy="457" r="100"/>
    <text class="lever-label medium"><tspan x="2054" y="437">REDUCE DUE/</tspan><tspan x="2054" y="464">OVERDUE</tspan><tspan x="2054" y="492">RECEIVABLE</tspan></text>

    <circle class="lever-receivables" cx="2314" cy="457" r="100"/>
    <text class="lever-label small"><tspan x="2314" y="439">ESTABLISH NEW</tspan><tspan x="2314" y="464">PAYMENT</tspan><tspan x="2314" y="488">CONDITIONS</tspan></text>

    <circle class="lever-payables" cx="754" cy="1061" r="100"/>
    <text class="lever-label medium"><tspan x="754" y="1041">OPTIMIZE</tspan><tspan x="754" y="1068">EXTERNAL</tspan><tspan x="754" y="1095">PURCHASING</tspan></text>

    <circle class="lever-payables" cx="2054" cy="1061" r="100"/>
    <text class="lever-label medium"><tspan x="2054" y="1026">REDUCE</tspan><tspan x="2054" y="1053">FINISHED</tspan><tspan x="2050" y="1081">GOODS</tspan><tspan x="2054" y="1109">STOCKS</tspan></text>

    <circle class="lever-payables" cx="2314" cy="1061" r="100"/>
    <text class="lever-label medium"><tspan x="2310" y="1053">REDUCE</tspan><tspan x="2314" y="1081">INVENTORY</tspan></text>
  </g>

  <!-- legend -->
  <g class="legend">
    <circle class="legend-dot-inventory" cx="1584" cy="1255" r="19"/>
    <text class="legend-label" x="1616" y="1263">INVENTORY</text>

    <circle class="legend-dot-payables" cx="1797" cy="1255" r="19"/>
    <text class="legend-label"><tspan x="1836" y="1263">PAYABLES AND</tspan><tspan x="1836" y="1288">PRE-PAYMENTS MADE</tspan></text>

    <circle class="legend-dot-receivables" cx="2121" cy="1255" r="19"/>
    <text class="legend-label"><tspan x="2160" y="1263">RECEIVABLES AND</tspan><tspan x="2160" y="1288">PRE-PAYMENTS RECEIVED</tspan></text>
  </g>
</svg>
</body>
</html>
```